At Home Pet Euthanasia - business cards & brand stationary

We already have a logo and the colors and a website. Need a business card designed that will be able to customized to multiple veterinarians who will be partnering with us. The feel needs to be compassionate, comforting with our tagline 'A Gift of Love at Home'. It will be 2 sides.
On the back our platform/partner vets will be customizing each business card with their own service areas, phone numbers, name and title. On the front, i would like to see experimentation with use of our photos, the logo, tagline and a description 'Peaceful and Compassionate At-Home Pet Euthanasia'

```html
<!DOCTYPE html>
<html lang="en">
<head>
<meta charset="UTF-8">
<title>Hearthway Business Card</title>
<link href="https://fonts.googleapis.com/css2?family=Montserrat:wght@600;700&family=Open+Sans:ital,wght@0,400;1,400&family=Oswald:wght@500&display=swap" rel="stylesheet">
<style>
  :root {
    --brand-blue: #7598c2;
    --ink: #1c1c1c;
    --paper: #ffffff;
    --backdrop: #2b2b2b;
    --photo-dark: #262626;
    --photo-mid: #5a5a5a;
    --photo-light: #8a8a8a;
    --rule: #9a9a9a;
  }
  * { box-sizing: border-box; margin: 0; padding: 0; }
  html, body { width: 1200px; height: 1040px; overflow: hidden; }
  body {
    background: radial-gradient(ellipse at center, #3a3a3a 0%, var(--backdrop) 70%, #1e1e1e 100%);
    position: relative;
    font-family: "Open Sans", Arial, sans-serif;
  }
  .card {
    position: absolute;
    left: 280px;
    width: 640px;
    height: 366px;
    border-radius: 0 64px 0 64px;
    overflow: hidden;
    box-shadow: 0 10px 28px rgba(0,0,0,0.55);
  }
  .card--front { top: 112px; }
  .card--back { top: 542px; background: var(--paper); }

  .front-photo {
    position: absolute; inset: 0;
    background:
      radial-gradient(ellipse at 38% 62%, var(--photo-light) 0%, transparent 38%),
      radial-gradient(ellipse at 20% 15%, #777 0%, transparent 30%),
      linear-gradient(160deg, var(--photo-mid) 0%, var(--photo-dark) 60%, #1a1a1a 100%);
  }
  .front-brand {
    position: absolute;
    right: 54px; bottom: 96px;
    display: flex; align-items: center; gap: 12px;
  }
  .brand-mark {
    width: 44px; height: 44px;
    border-radius: 50%;
    background: var(--brand-blue);
  }
  .brand-name {
    font-family: "Montserrat", Arial, sans-serif;
    font-weight: 700;
    color: var(--brand-blue);
    font-size: 50px;
    line-height: 1;
    letter-spacing: -0.5px;
  }
  .front-description {
    position: absolute;
    right: 60px; bottom: 28px;
    width: 300px;
    text-align: center;
    font-family: "Oswald", "Arial Narrow", sans-serif;
    font-weight: 500;
    color: var(--paper);
    font-size: 19px;
    line-height: 1.3;
    text-transform: uppercase;
  }

  .back-brand {
    position: absolute;
    left: 40px; top: 88px;
    width: 300px;
    display: flex; flex-direction: column; align-items: center;
  }
  .back-brand .brand-mark { width: 96px; height: 96px; margin-bottom: 18px; }
  .back-brand .brand-name { font-size: 54px; }
  .back-tagline {
    margin-top: 8px;
    font-style: italic;
    color: var(--brand-blue);
    font-size: 17px;
  }
  .back-divider {
    position: absolute;
    left: 350px; top: 78px;
    width: 1px; height: 210px;
    background: var(--rule);
  }
  .contact {
    position: absolute;
    left: 372px; top: 80px;
    color: var(--ink);
    font-size: 17px;
    line-height: 1.3;
  }
  .contact-name {
    font-family: "Montserrat", Arial, sans-serif;
    font-weight: 700;
    color: var(--brand-blue);
    font-size: 24px;
    letter-spacing: 1px;
    line-height: 1.1;
  }
  .contact-title { font-size: 17px; margin-bottom: 10px; }
  .contact-line { display: flex; align-items: center; gap: 8px; }
  .contact-line svg { width: 16px; height: 16px; flex: none; }
  .contact-line .accent { color: var(--brand-blue); }
  .contact-address { margin-top: 8px; }
</style>
</head>
<body>
  <section class="card card--front">
    <div class="front-photo" role="img" aria-label="Black and white photo of a person gently stroking a speckled dog lying on the floor"></div>
    <div class="front-brand">
      <span class="brand-mark"></span>
      <span class="brand-name">Hearthway</span>
    </div>
    <p class="front-description">Peaceful and compassionate<br>at-home pet euthanasia</p>
  </section>

  <section class="card card--back">
    <div class="back-brand">
      <span class="brand-mark"></span>
      <span class="brand-name">Hearthway</span>
      <span class="back-tagline">A gift of love at home.</span>
    </div>
    <div class="back-divider"></div>
    <div class="contact">
      <p class="contact-name">Daniel Moreau</p>
      <p class="contact-title">Managing Director</p>
      <p class="contact-line">
        <svg viewBox="0 0 16 16" aria-hidden="true"><path d="M4 1.5 L6.5 4.5 L5 6.5 Q6.5 9.5 9.5 11 L11.5 9.5 L14.5 12 L13 14.5 Q6 14 1.5 3 Z" fill="none" stroke="#7598c2" stroke-width="1.4" stroke-linejoin="round"/></svg>
        044-987 654 321
      </p>
      <p class="contact-line">
        <svg viewBox="0 0 16 16" aria-hidden="true"><rect x="1" y="3" width="14" height="10" fill="none" stroke="#7598c2" stroke-width="1.4"/><path d="M1 3 L8 9 L15 3" fill="none" stroke="#7598c2" stroke-width="1.4"/></svg>
        hello@hearthway.com
      </p>
      <p class="contact-line">
        <svg viewBox="0 0 16 16" aria-hidden="true"><circle cx="8" cy="8" r="6.5" fill="none" stroke="#7598c2" stroke-width="1.3"/><ellipse cx="8" cy="8" rx="3" ry="6.5" fill="none" stroke="#7598c2" stroke-width="1.1"/><path d="M1.5 8 H14.5 M2.5 5 H13.5 M2.5 11 H13.5" stroke="#7598c2" stroke-width="1.1"/></svg>
        <span>www.<span class="accent">hearthway</span>.com</span>
      </p>
      <p class="contact-address">421, Address line goes here<br>45452, Country Name</p>
    </div>
  </section>
</body>
</html>
```